Website design for luxury private hair salon

I'm looking for someone to use my Logo and build me a website for my webpage www.corsetresses.com.au (You can have a look at it as it has every detail I need included on it already), however I want a fresh new appearance and it to look and feel super stylish.

I am thinking colours in black, with silver or white, beautiful hair images like the ones you'll see on the current webpage - the price list as per what you already see.

I will include a copy of my biz card on here, so you can see the feel of the card, and design a website with a similar feel. It is matt black with a foil silver.

Modern, but classic and fresh. I will also need you to be able to publish it to my URL for me as I have no idea how to do this. I need it up and running pronto!

The website will need to be able to be read clearly on all devices incluing smart phones and ipads. The URL is currently registered and hosted by Norvel Web

Thinking a Home Page - large logo etc and write up on who and what we offer
Services/Price List page - as per the price list on my current webpage
Contact Page - with a built in contact form.

Target Market(s)

Middle aged, fashionable, stylish women and men who enjoy luxury hair care and styling in an upmarket location.

Industry/Entity Type

Hair And Beauty

Number of Pages Required

3 page

Font styles to use
Other font styles liked:
• see my images for my current logo

Colors
000000
b2b2b2
a54499

Requirements
Must have
• Style
• Fast turnaround
• Be viewable on all devices, PC, ipads, smart phones
• Designer able to upload it so its a running website for me to my URL
Nice to have
• Just a really feminine, stylish website which is easy to read and shows some beautiful images of perfect hair
Should not have
• Browns, reds or orange colours.

```html
<!DOCTYPE html>
<html lang="en">
<head>
<meta charset="utf-8">
<title>Maison Hair &amp; Body</title>
<link href="https://fonts.googleapis.com/css2?family=Raleway:wght@300;400;600;700&display=swap" rel="stylesheet">
<style>
:root{
  --bg:#1a1a1a;
  --ink:#ffffff;
  --silver:#b2b2b2;
  --muted:#3c3c3c;
  --line:#8a8a8a;
  --hero-a:#0e0b0b;
  --hero-b:#2c2424;
  --hero-c:#5a4a46;
}
*{margin:0;padding:0;box-sizing:border-box}
html,body{width:713px;height:1200px;overflow:hidden;background:var(--bg)}
body{font-family:"Raleway",sans-serif;color:var(--ink);position:relative}
.abs{position:absolute}

.hero{left:0;top:0;width:713px;height:348px;
  background:radial-gradient(ellipse at 78% 55%,var(--hero-c) 0%,var(--hero-b) 30%,var(--hero-a) 75%)}
.brand-small{left:112px;top:22px;font-size:12px;font-weight:400;color:var(--silver);letter-spacing:.5px}
.nav{top:19px;left:501px;display:flex;gap:0}
.nav a{position:absolute;font-size:7px;font-weight:600;color:var(--ink);text-decoration:none;white-space:nowrap}
.nav a.active{border-bottom:1px solid var(--ink);padding-bottom:2px}
.brand-large{left:0;width:713px;top:130px;text-align:center;font-size:54px;font-weight:300;color:var(--silver);letter-spacing:2px}

.welcome-title{left:0;width:713px;top:378px;text-align:center;font-size:23px;font-weight:700}
.welcome-text{left:203px;width:309px;top:413px;text-align:center;font-size:8.4px;line-height:11.5px;font-weight:400}

.section-title{left:152px;font-size:21px;font-weight:700}
.section-title span{font-weight:300}

.service{width:120px}
.service .num{font-size:21px;font-weight:300;color:var(--muted);line-height:1}
.service .label{font-size:6.5px;font-weight:700;margin-top:5px}

.gallery{left:0;top:800px;width:713px;height:209px;display:grid;grid-template-columns:repeat(5,1fr);grid-template-rows:repeat(2,1fr)}
.tile{width:100%;height:100%}

.phone-caption{left:152px;top:1079px;font-size:7px}
.phone{left:152px;font-size:13px;font-weight:300;color:var(--silver);letter-spacing:.3px}
.field{border-bottom:1px solid var(--line);border-left:1px solid var(--line);height:9px;font-size:6px;font-style:italic;color:var(--silver);padding-left:3px;line-height:7px}
.send{left:450px;top:1155px;width:36px;height:15px;border:1px solid var(--ink);border-radius:8px;font-size:6px;font-weight:600;text-align:center;line-height:13px}
.footnote{left:152px;top:1162px;font-size:4.5px;color:var(--silver)}
</style>
</head>
<body>

<div class="abs hero" role="img" aria-label="Hero photograph of a woman with long glossy dark hair"></div>
<div class="abs brand-small">Maison</div>
<nav class="abs nav">
  <a class="active" style="left:0">Home</a>
  <a style="left:33px">Services</a>
  <a style="left:74px">Price List</a>
  <a style="left:117px">Contacts</a>
</nav>
<div class="abs brand-large">Maison Hair &amp; Body</div>

<h1 class="abs welcome-title">Welcome</h1>
<p class="abs welcome-text">"We pride ourselves on being able to offer a private salon experience to our clients in the exclusive suburb of Westbrook, where your hair design and colouring needs will be met with years of experience and current industry training and knowledge".</p>

<h2 class="abs section-title" style="top:524px">Services</h2>
<div class="abs service" style="left:152px;top:568px"><div class="num">01/</div><div class="label">Hair Cut</div></div>
<div class="abs service" style="left:290px;top:568px"><div class="num">02/</div><div class="label">Colouring</div></div>
<div class="abs service" style="left:429px;top:568px"><div class="num">03/</div><div class="label">Highlighting</div></div>
<div class="abs service" style="left:152px;top:652px"><div class="num">04/</div><div class="label">Extensions</div></div>
<div class="abs service" style="left:290px;top:652px"><div class="num">05/</div><div class="label">Straightening</div></div>
<div class="abs service" style="left:429px;top:652px"><div class="num">06/</div><div class="label">Bridal Treatments</div></div>

<h2 class="abs section-title" style="top:760px">Our <span>Gallery</span></h2>
<div class="abs gallery">
  <div class="tile" role="img" aria-label="Blonde voluminous hair portrait" style="background:linear-gradient(135deg,#b89a6c,#6e5a48)"></div>
  <div class="tile" role="img" aria-label="Dark flowing hair in profile" style="background:linear-gradient(135deg,#2a2424,#4a3c3a)"></div>
  <div class="tile" role="img" aria-label="Sleek straight brunette hair" style="background:linear-gradient(135deg,#e8e4e2,#6a4c40)"></div>
  <div class="tile" role="img" aria-label="Dark wavy hair portrait" style="background:linear-gradient(135deg,#1c1818,#5a4a44)"></div>
  <div class="tile" role="img" aria-label="Long dark hair portrait" style="background:linear-gradient(135deg,#3a3636,#6a5650)"></div>
  <div class="tile" role="img" aria-label="Long hair outdoors in greenery" style="background:linear-gradient(135deg,#6c7a3c,#3c3424)"></div>
  <div class="tile" role="img" aria-label="Dark hair blowing sideways" style="background:linear-gradient(135deg,#1e1a1a,#4c3e3c)"></div>
  <div class="tile" role="img" aria-label="Blonde curled hair portrait" style="background:linear-gradient(135deg,#9c8a70,#4e4644)"></div>
  <div class="tile" role="img" aria-label="Flowing auburn hair on teal backdrop" style="background:linear-gradient(135deg,#2e6a64,#6a3024)"></div>
  <div class="tile" role="img" aria-label="Dark straight hair portrait" style="background:linear-gradient(135deg,#4a4444,#2a2222)"></div>
</div>

<h2 class="abs section-title" style="top:1038px">Contacts</h2>
<div class="abs phone-caption">Free phone :</div>
<div class="abs phone" style="top:1090px">ANNA&nbsp; 0400 555 218</div>
<div class="abs phone" style="top:1108px">KATE&nbsp; 0400 555 734</div>

<div class="abs field" style="left:380px;top:1088px;width:83px">Name</div>
<div class="abs field" style="left:472px;top:1088px;width:81px">E-mail</div>
<div class="abs field" style="left:380px;top:1133px;width:173px">Message</div>
<div class="abs send">Send</div>

<div class="abs footnote">Maison Hair &amp; Body © 2016. Privacy Policy</div>

</body>
</html>
```